indépendant en tant que Massothérapeute et Préparateur Mental, j'ai besoin de ...

Massothérapeute et préparateur mental indépendant, je recherche une carte de visite sobre et dynamique, sans images liées au massage ou à la préparation mentale mais intégrant mon logo. Les couleurs que j'aime bien sont : Blanc, gris, anthracite, noir et jaune

Contact Information for Business Card

carte de préférence Horizontale
neutre qui puisse toucher le deux domaines Massothérapie et préparation mentale

Requirements
Must have
• mon projet doit intégrer au recto:
LOGO
Loïc Bardèze
078 513 26 48
info@loicbardeze.ch
et éventuellement www.loicbardeze.ch

et au verso les deux adresses:

Chemin des Ormilles 7B
1400 Yverdon-les-Bains

Route de la Gravière 9
1700 Fribourg

Should not have
• mon projet ne doit pas contenir d'image en liens avec le massage ni la préparation mentale.

```html
<!DOCTYPE html>
<html lang="fr">
<head>
<meta charset="utf-8">
<title>Loïc Bardèze – cartes de visite</title>
<link rel="stylesheet" href="https://fonts.googleapis.com/css2?family=Arimo:wght@400&family=Montserrat:wght@400;600;700&display=swap">
<style>
  :root {
    --page: #3a3a3a;
    --card: #232223;
    --white: #f2f2f2;
    --grey-line: #5c5c5c;
    --yellow: #f2d40e;
  }
  * { margin: 0; padding: 0; box-sizing: border-box; }
  html, body { width: 1200px; height: 1015px; overflow: hidden; }
  body {
    background: var(--page);
    display: flex;
    flex-direction: column;
    align-items: center;
    justify-content: center;
    gap: 45px;
    font-family: "Arimo", Arial, sans-serif;
  }
  .card {
    position: relative;
    width: 700px;
    height: 400px;
    background: var(--card);
    box-shadow: 0 10px 30px rgba(0,0,0,.45);
    overflow: hidden;
  }
  .card__band {
    position: absolute;
    left: 0; right: 0; bottom: 0;
    height: 12px;
    background: var(--yellow);
  }
  .brand {
    position: absolute;
    top: 120px;
    left: 300px;
    color: var(--white);
    font-family: "Montserrat", sans-serif;
  }
  .brand__name {
    font-weight: 600;
    font-size: 34px;
    letter-spacing: .5px;
    line-height: 1;
  }
  .brand__tagline {
    margin-top: 6px;
    font-weight: 400;
    font-size: 10.5px;
    letter-spacing: 1.2px;
    text-transform: uppercase;
  }
  .rule {
    position: absolute;
    height: 1px;
    background: var(--grey-line);
  }
  .card--back .rule { left: 40px; right: 30px; top: 235px; }
  .addresses {
    position: absolute;
    left: 52px;
    top: 258px;
    color: var(--white);
    font-size: 20px;
    line-height: 1.15;
  }
  .address + .address { margin-top: 14px; }
  .card--front .rule { left: 390px; right: 30px; top: 262px; }
  .holder {
    position: absolute;
    left: 52px;
    top: 245px;
    color: var(--yellow);
    font-family: "Montserrat", sans-serif;
    font-weight: 700;
    font-size: 32px;
    letter-spacing: .5px;
  }
  .contacts {
    position: absolute;
    left: 56px;
    top: 292px;
    list-style: none;
    color: var(--white);
    font-size: 19px;
    line-height: 1.3;
  }
  .contacts li { display: flex; align-items: center; gap: 10px; }
  .contacts svg { width: 18px; height: 18px; fill: none; stroke: var(--yellow); stroke-width: 2; }
</style>
</head>
<body>

<section class="card card--back" aria-label="Verso">
  <div class="brand">
    <div class="brand__name">Loïc Bardèze</div>
    <div class="brand__tagline">Massothérapeute / Préparateur mental</div>
  </div>
  <div class="rule"></div>
  <div class="addresses">
    <p class="address">Chemin des Ormilles 7B<br>1400 Yverdon-les-Bains</p>
    <p class="address">Route de la Gravière 9<br>1700 Freiburg</p>
  </div>
  <div class="card__band"></div>
</section>

<section class="card card--front" aria-label="Recto">
  <div class="brand">
    <div class="brand__name">Loïc Bardèze</div>
    <div class="brand__tagline">Massothérapeute / Préparateur mental</div>
  </div>
  <div class="rule"></div>
  <h1 class="holder">LOÏC BARDÈZE</h1>
  <ul class="contacts">
    <li>
      <svg viewBox="0 0 24 24" aria-hidden="true"><path d="M5 3h4l2 5-3 2a12 12 0 0 0 6 6l2-3 5 2v4a2 2 0 0 1-2 2A17 17 0 0 1 3 5a2 2 0 0 1 2-2z"/></svg>
      078 513 26 48
    </li>
    <li>
      <svg viewBox="0 0 24 24" aria-hidden="true"><rect x="3" y="5" width="18" height="14"/><path d="M3 5l9 8 9-8"/></svg>
      info@loicbardeze.ch
    </li>
    <li>
      <svg viewBox="0 0 24 24" aria-hidden="true"><circle cx="12" cy="12" r="9"/><path d="M3 12h18M12 3c3 3 3 15 0 18M12 3c-3 3-3 15 0 18"/></svg>
      www.loicbardeze.ch
    </li>
  </ul>
  <div class="card__band"></div>
</section>

</body>
</html>
```